Local massage therapist needs some new marketing material

Hi there! I am a massage therapist here in Denver, CO in Alder Bend(shopping and art district) of the city. My business is called Lumo Bodywork of Denver. My practice has an eastern influence and I do reflexology, thai massage and use Chinese herbs, etc. I know all my clients and pay close attention to details. I am also very respectful of tradition and it shows in how I work. I tend to like modern, clean, fun, Asian designs. I am wanting a new business card and brochure. I have a logo and branding for my business that I want used in the design. Currently, the sign for my building is purple and I think my logo was designed to be purple. I will attach pictures of it and can send whatever files are necessary so it can be integrated into the brochure, etc. I like the purple but open to using other colors as well. Thanks!
My website is lumobodyworkofdenver.example where info can be gathered about me and services/fees for brochure.
Updates

Just increased budget. Please see new feedback in discussion thread.

Thanks!

                                       HEY ALL,

Just wanted to let you know that I made a change to my website. It is on the Prices Page. I no longer have the frequent  flyer prices but I added discounts. Let me know if you have any questions. Thanks so much!

Target Market(s)

healthy, urban, educated, upper middle class, yogis

Industry/Entity Type

Marketing

Requirements
Must have
• logo stays purple
Should not have
• not too busy

```html
<!DOCTYPE html>
<html lang="en">
<head>
<meta charset="utf-8">
<title>Lumo Bodywork of Denver – Business Card</title>
<link rel="stylesheet" href="https://fonts.googleapis.com/css2?family=Open+Sans:ital,wght@0,300;0,400;0,600;0,700;1,400&display=swap">
<style>
  :root{
    --purple:#5f2d91;
    --purple-soft:#e9e2f1;
    --charcoal:#333333;
    --text-grey:#555555;
    --rule-grey:#b5b5b5;
    --card:#ffffff;
    --backdrop:#eeeceb;
  }
  *{box-sizing:border-box;margin:0;padding:0}
  html,body{width:1200px;height:720px;overflow:hidden}
  body{background:var(--backdrop);font-family:"Open Sans",Arial,sans-serif;position:relative}
  .card{position:absolute;top:205px;width:540px;height:309px;background:var(--card);
        box-shadow:0 2px 10px rgba(0,0,0,.12);overflow:hidden}
  .card--front{left:40px}
  .card--back{left:620px}

  /* front */
  .brand{position:absolute;left:30px;top:28px;width:180px;text-align:center}
  .brand__dot{width:60px;height:60px;border-radius:50%;background:var(--purple);margin:0 auto 12px}
  .brand__name{font-size:46px;font-weight:300;letter-spacing:6px;color:var(--purple);line-height:1}
  .divider{position:absolute;left:228px;top:26px;width:1px;height:118px;background:var(--rule-grey)}
  .contact{position:absolute;left:240px;top:30px;list-style:none;font-size:12px;color:var(--text-grey)}
  .contact li{display:flex;align-items:center;gap:6px;height:18px}
  .contact li.contact__address{margin-top:16px}
  .contact svg{width:11px;height:11px;fill:var(--purple);flex:none}
  .swoosh{position:absolute;left:0;top:0;width:540px;height:309px}
  .person{position:absolute;left:70px;top:250px;width:180px;color:#fff;text-align:center}
  .person__name{font-size:17px;font-weight:700;line-height:1.2}
  .person__title{font-size:12px;font-weight:400;opacity:.9}

  /* back */
  .watermark{position:absolute;left:175px;top:40px;width:200px;height:200px;border-radius:50%;
             background:var(--purple-soft);opacity:.55}
  .appt{position:absolute;inset:0;color:var(--charcoal)}
  .appt__heading{position:absolute;left:150px;top:42px;font-size:15px;font-weight:700;color:var(--purple);letter-spacing:.5px}
  .appt__rule{position:absolute;left:350px;top:54px;width:150px;border-top:1px solid var(--text-grey)}
  .field{position:absolute;font-size:15px;display:flex;align-items:flex-end;gap:6px;line-height:1.2}
  .field__line{display:inline-block;border-bottom:1px dotted var(--text-grey);height:14px}
  .field--name{left:40px;top:110px}
  .field--time{left:290px;top:92px}
  .field--date{left:40px;top:150px}
  .hours{position:absolute;left:0;right:0;top:184px;text-align:center;font-size:15px;line-height:1.5}
  .notice{position:absolute;left:0;right:0;top:254px;text-align:center;font-size:14px;font-style:italic;color:#777}
</style>
</head>
<body>

<section class="card card--front" aria-label="Business card front">
  <div class="brand">
    <div class="brand__dot"></div>
    <div class="brand__name">LUMO</div>
  </div>
  <div class="divider"></div>
  <ul class="contact">
    <li><svg viewBox="0 0 24 24"><path d="M6.6 10.8a15.1 15.1 0 0 0 6.6 6.6l2.2-2.2a1 1 0 0 1 1-.25 11.4 11.4 0 0 0 3.6.57 1 1 0 0 1 1 1V20a1 1 0 0 1-1 1A17 17 0 0 1 3 4a1 1 0 0 1 1-1h3.5a1 1 0 0 1 1 1c0 1.25.2 2.450 .57 3.57a1 1 0 0 1-.25 1z"/></svg>303.555.0148</li>
    <li><svg viewBox="0 0 24 24"><path d="M2 5h20v14H2zm2 2v.5l8 5 8-5V7l-8 5z"/></svg>info@lumobodyworkofdenver.example</li>
    <li><svg viewBox="0 0 24 24"><circle cx="12" cy="12" r="10"/></svg>www.lumobodyworkofdenver.example</li>
    <li class="contact__address">1450 E Alder Ave, Denver, CO 80206</li>
  </ul>
  <svg class="swoosh" viewBox="0 0 540 309" aria-hidden="true">
    <path d="M0 158 C120 200 260 222 540 104 L540 116 C260 236 120 212 0 168 Z" fill="var(--charcoal)"/>
    <path d="M0 176 C120 218 260 240 540 124 L540 309 L0 309 Z" fill="var(--purple)"/>
  </svg>
  <div class="person">
    <div class="person__name">Your Name</div>
    <div class="person__title">Title</div>
  </div>
</section>

<section class="card card--back" aria-label="Appointment card back">
  <div class="watermark" role="img" aria-label="Faint brand mark decoration"></div>
  <div class="appt">
    <h2 class="appt__heading">YOUR APPOINTMENT</h2>
    <span class="appt__rule"></span>
    <div class="field field--time">Time : <span class="field__line" style="width:110px"></span> am / pm</div>
    <div class="field field--name">Name : <span class="field__line" style="width:150px"></span></div>
    <div class="field field--date">Date : <span class="field__line" style="width:150px"></span></div>
    <p class="hours">Tues - Fri 10am - 8pm Sat 10am-5pm<br>(Appointments required) No walk-ins please.</p>
    <p class="notice">We appreciate a 24 hr. notice for cancellations</p>
  </div>
</section>

</body>
</html>
```